Pool Screen Enclosure Building a Career Boot Camp!

Looking to Host a Boot Camp for people looking for a career or looking to change careers. We Design, Manufacture and Install Custom Pool Screen Enclosures. We have a training program to allow Non Experienced motivated people the chance at a great career that will provide a great living for them and their family. This will be a paid boot camp, week long, we provide all the initial training for them to make a transition into our business. This will be 5 days of training with a guaranteed job to start the following Monday.... This is good for both someone with no construction experience or someone with construction experience that wants to upgrade their current job.
Paid Boot Camp
transition to a full time job with great pay
Benefits include Health Insurance, Dental and Vision, 401K, we provide the tools and training.

```html
<!DOCTYPE html>
<html lang="en">
<head>
<meta charset="utf-8">
<title>Paid Boot Camp Flyer</title>
<link href="https://fonts.googleapis.com/css2?family=Archivo+Black&family=Montserrat:ital,wght@0,400;0,600;0,700;0,800;1,600&display=swap" rel="stylesheet">
<style>
  :root{
    --yellow:#fff212;
    --green:#17782c;
    --lime:#8fdc3a;
    --black:#0b0b0b;
    --white:#ffffff;
    --ink:#1a1a1a;
    --stage:#d9d6d2;
    --photo-sky:#b9c3cc;
    --photo-pool:#6fa8a4;
  }
  *{box-sizing:border-box;margin:0;padding:0}
  html,body{width:1200px;height:800px;overflow:hidden;background:var(--stage);font-family:"Montserrat",sans-serif}
  .flyer{position:absolute;left:300px;top:10px;width:600px;height:780px;background:var(--white);overflow:hidden;box-shadow:0 4px 18px rgba(0,0,0,.25)}

  .hero-photo{position:absolute;left:0;top:0;width:600px;height:290px;
    background:linear-gradient(180deg,var(--photo-sky) 0%,#d8c8c4 45%,#7f8f6a 62%,var(--photo-pool) 80%,#8e7d6c 100%)}
  .band{position:absolute;left:0;top:270px;width:600px;height:190px;background:var(--yellow);clip-path:polygon(0 12%,100% 0,100% 100%,0 100%)}
  .band-tail{position:absolute;left:0;top:459px;width:325px;height:56px;background:var(--yellow)}
  .band-photo{position:absolute;top:292px;height:112px;width:200px;clip-path:polygon(20% 0,100% 0,80% 100%,0 100%)}
  .band-photo.one{left:24px;background:linear-gradient(160deg,#7fa9d8,#c8d3dc 55%,#7d8a6c)}
  .band-photo.two{left:196px;background:linear-gradient(170deg,#e9e7e2,#b59c86 60%,#d9d4cc)}
  .band-photo.three{left:368px;background:linear-gradient(165deg,#9fbde0,#d7dde0 50%,#8f9477)}

  .title{position:absolute;left:24px;top:410px;font-family:"Archivo Black",sans-serif;font-size:44px;line-height:1;color:var(--black);letter-spacing:.5px;white-space:nowrap}

  .intro{position:absolute;left:22px;top:466px;width:292px;font-size:11.5px;font-weight:800;line-height:1.3;color:var(--ink)}

  .services{position:absolute;left:22px;top:524px;width:292px}
  .services-tab{display:inline-block;background:var(--green);color:var(--yellow);font-weight:800;font-size:14px;padding:4px 26px 4px 12px;clip-path:polygon(0 0,88% 0,100% 100%,0 100%)}
  .services-rule{height:2px;background:var(--green);margin-top:-2px}
  .services-list{list-style:none;margin-top:8px}
  .services-list li{position:relative;padding-left:18px;font-size:10px;line-height:1.35;color:var(--ink);margin-bottom:6px}
  .services-list li svg{position:absolute;left:0;top:2px}

  .offer{position:absolute;left:330px;top:462px;width:252px;height:232px;background:var(--green);border-radius:12px;padding:11px 13px;color:var(--white)}
  .offer-text{font-size:9.5px;font-weight:700;line-height:1.35}
  .offer-text em{font-style:normal;color:var(--yellow)}
  .offer-rule{height:1px;background:rgba(255,255,255,.5);margin:8px 0 6px}
  .benefits-head{font-size:12px;font-weight:800;color:var(--white);margin-bottom:5px}
  .benefits{display:grid;grid-template-columns:1fr 1fr;gap:6px 8px}
  .benefit{display:flex;align-items:center;gap:5px;font-size:8.5px;line-height:1.2}
  .benefit svg{flex:none}

  .footer-green{position:absolute;left:300px;top:712px;width:300px;height:68px;background:var(--green);clip-path:polygon(8% 0,100% 0,100% 100%,0 100%)}
  .contacts{position:absolute;left:345px;top:718px;font-size:9px;font-style:normal;color:var(--white);line-height:1.75}
  .contacts span{display:inline-flex;align-items:center;gap:4px;margin-right:8px}

  .footer-black{position:absolute;left:0;top:702px;width:340px;height:78px;background:var(--black);border-radius:0 40px 0 0}
  .brand{position:absolute;left:28px;top:718px;display:flex;align-items:center;gap:10px}
  .brand-dot{width:28px;height:28px;border-radius:50%;background:var(--lime)}
  .brand-name{font-size:21px;font-weight:700;color:var(--lime);white-space:nowrap}
  .tagline{position:absolute;left:78px;top:752px;font-size:10px;font-style:italic;font-weight:600;color:var(--yellow)}
</style>
</head>
<body>
<main class="flyer">
  <div class="hero-photo" role="img" aria-label="Photo of a screened pool enclosure beside a lake"></div>
  <div class="band"></div>
  <div class="band-tail"></div>
  <div class="band-photo one" role="img" aria-label="Photo of installers working on an enclosure roof"></div>
  <div class="band-photo two" role="img" aria-label="Photo of a team reviewing plans together"></div>
  <div class="band-photo three" role="img" aria-label="Photo of an enclosure frame under construction"></div>

  <h1 class="title">PAID BOOT CAMP</h1>
  <p class="intro">Looking to Host a Boot Camp for people looking for a career or looking to change careers.</p>

  <section class="services">
    <div class="services-tab">OUR SERVICES</div>
    <div class="services-rule"></div>
    <ul class="services-list">
      <li><svg width="11" height="11" viewBox="0 0 11 11"><circle cx="5.5" cy="5.5" r="5.5" fill="var(--green)"/><path d="M3 5.7l1.7 1.6L8 4" stroke="#fff" stroke-width="1.4" fill="none"/></svg>We Design, Manufacture and Install Custom Pool Screen Enclosures.</li>
      <li><svg width="11" height="11" viewBox="0 0 11 11"><circle cx="5.5" cy="5.5" r="5.5" fill="var(--green)"/><path d="M3 5.7l1.7 1.6L8 4" stroke="#fff" stroke-width="1.4" fill="none"/></svg>This will be a paid boot camp, week long, we provide all the initial training for them to make a transition into our business.</li>
      <li><svg width="11" height="11" viewBox="0 0 11 11"><circle cx="5.5" cy="5.5" r="5.5" fill="var(--green)"/><path d="M3 5.7l1.7 1.6L8 4" stroke="#fff" stroke-width="1.4" fill="none"/></svg>We have a training program to allow Non Experienced motivated people the chance at a great career that will provide a great living for them and their family.</li>
    </ul>
  </section>

  <section class="offer">
    <p class="offer-text">This will be <em>5 DAYS</em> of training with a <em>GUARANTEED JOB</em> to start the following <em>MONDAY</em>.... This is good for both someone with no construction experience or someone with construction experience that wants to upgrade their current job.</p>
    <div class="offer-rule"></div>
    <h2 class="benefits-head">Benefits</h2>
    <div class="benefits">
      <div class="benefit"><svg width="15" height="15" viewBox="0 0 16 16"><circle cx="8" cy="8" r="6.5" stroke="var(--yellow)" stroke-width="1.4" fill="none"/></svg>Transition to a full time job with great pay</div>
      <div class="benefit"><svg width="15" height="15" viewBox="0 0 16 16"><rect x="2" y="3" width="12" height="10" rx="1.5" stroke="var(--yellow)" stroke-width="1.4" fill="none"/></svg>we provide the tools &amp; training.</div>
      <div class="benefit"><svg width="15" height="15" viewBox="0 0 16 16"><rect x="2" y="2" width="12" height="12" rx="2" stroke="var(--yellow)" stroke-width="1.4" fill="none"/><path d="M8 5v6M5 8h6" stroke="var(--yellow)" stroke-width="1.4"/></svg>Health Insurance</div>
      <div class="benefit"><svg width="15" height="15" viewBox="0 0 16 16"><circle cx="8" cy="8" r="6.5" stroke="var(--yellow)" stroke-width="1.4" fill="none"/><path d="M8 4v8" stroke="var(--yellow)" stroke-width="1.4"/></svg>401K</div>
      <div class="benefit"><svg width="15" height="15" viewBox="0 0 16 16"><circle cx="8" cy="8" r="6.5" stroke="var(--yellow)" stroke-width="1.4" fill="none"/><circle cx="8" cy="8" r="2" fill="var(--yellow)"/></svg>Dental and Vision</div>
    </div>
  </section>

  <div class="footer-green"></div>
  <address class="contacts">
    <span><svg width="10" height="12" viewBox="0 0 10 12"><path d="M5 11.5S1 7 1 4.5a4 4 0 018 0C9 7 5 11.5 5 11.5z" fill="none" stroke="#fff" stroke-width="1.2"/><circle cx="5" cy="4.5" r="1.3" fill="#fff"/></svg>1420 Harbor View Road, Palm Shore FL 34900</span><br>
    <span><svg width="12" height="10" viewBox="0 0 12 10"><rect x=".6" y=".6" width="10.8" height="8.8" rx="1" fill="none" stroke="#fff" stroke-width="1.2"/><path d="M1 1l5 4 5-4" fill="none" stroke="#fff" stroke-width="1.2"/></svg>hello@lanaicraftworks.com</span>
    <span><svg width="11" height="11" viewBox="0 0 11 11"><path d="M2 1l2 .3.8 2.3-1.3 1a6 6 0 002.9 2.9l1-1.3 2.3.8.3 2-1.2 1C4.6 9.8 1.2 6.4 1 2.2z" fill="#fff"/></svg>555-014-2278</span><br>
    <span><svg width="11" height="11" viewBox="0 0 11 11"><circle cx="5.5" cy="5.5" r="4.9" fill="none" stroke="#fff" stroke-width="1.1"/><path d="M.6 5.5h9.8M5.5.6c-2.4 3-2.4 6.8 0 9.8M5.5.6c2.4 3 2.4 6.8 0 9.8" fill="none" stroke="#fff" stroke-width=".9"/></svg>www.lanaicraftworks.com</span>
  </address>

  <div class="footer-black"></div>
  <div class="brand">
    <div class="brand-dot"></div>
    <div class="brand-name">Lanai Craft Works</div>
  </div>
  <p class="tagline">“Screen it in, live it out”</p>
</main>
</body>
</html>
```